Wall poster for our in home gym.

I would like a poster that has a unique logo or icon for our in home Gym. We want to call it "The KOR" or "The Holl KOR" given our last name is Hollen. We work out with Dumbells, barbells, kettle bells, jump rope, sleds, tires, sledge hammers, pullups, pushups..etc...
The room is Half way up the wall red, the rest white with green artificial turf...
Reason: I am going to eliminate all those I dont want and then suggest some changes to those I like.
Gym

```html
<!DOCTYPE html>
<html lang="en">
<head>
<meta charset="UTF-8">
<title>The Holl KOR – Wall Poster</title>
<link rel="stylesheet" href="https://fonts.googleapis.com/css2?family=Fredoka:wght@600;700&family=Arimo:ital,wght@1,400;1,700&family=Archivo+Black&display=swap">
<style>
  :root {
    --backdrop-dark: #140606;
    --backdrop-mid: #2a1210;
    --skin-light: #e8a882;
    --skin-mid: #c97f5c;
    --skin-shadow: #8a4a32;
    --title-yellow: #f0b800;
    --band-yellow: #ebbd27;
    --band-light: #ecc95a;
    --brand-red: #d8352a;
    --tag-green: #2f8a2c;
    --ink-black: #111111;
  }
  * { margin: 0; padding: 0; box-sizing: border-box; }
  html, body { width: 900px; height: 1200px; overflow: hidden; background: #ffffff; }
  .poster {
    position: relative;
    width: 900px;
    height: 1200px;
    overflow: hidden;
    font-family: "Fredoka", sans-serif;
  }
  .hero-photo {
    position: absolute;
    left: 0; top: 0;
    width: 900px; height: 860px;
    background:
      radial-gradient(ellipse 70% 40% at 60% 68%, var(--skin-light) 0%, var(--skin-mid) 45%, rgba(201,127,92,0) 75%),
      linear-gradient(180deg, var(--backdrop-dark) 0%, var(--backdrop-mid) 100%);
  }
  .title-the {
    position: absolute;
    left: 285px; top: 352px;
    font-weight: 700;
    font-size: 104px;
    line-height: 1;
    color: var(--title-yellow);
  }
  .title-name {
    position: absolute;
    left: 160px; top: 500px;
    width: 460px;
    text-align: center;
    font-weight: 700;
    font-size: 190px;
    line-height: 1;
    color: var(--skin-mid);
    text-shadow:
      -3px -3px 4px rgba(255,220,190,0.55),
      4px 5px 8px rgba(90,40,20,0.6),
      0 0 24px rgba(138,74,50,0.35);
  }
  .band {
    position: absolute;
    left: 0; top: 860px;
    width: 900px; height: 340px;
    background: linear-gradient(90deg, var(--band-yellow) 0%, var(--band-light) 50%, var(--band-yellow) 100%);
  }
  .brand-name {
    position: absolute;
    left: 240px; top: 862px;
    font-weight: 700;
    font-size: 140px;
    line-height: 1;
    letter-spacing: 2px;
    color: var(--brand-red);
  }
  .tagline {
    position: absolute;
    left: 158px; top: 1082px;
    font-family: "Arimo", sans-serif;
    font-style: italic;
    font-size: 48px;
    line-height: 1.2;
    color: var(--tag-green);
    white-space: nowrap;
  }
  .tagline-strong {
    font-family: "Archivo Black", sans-serif;
    font-size: 42px;
    color: var(--ink-black);
    letter-spacing: -1px;
  }
</style>
</head>
<body>
  <main class="poster">
    <div class="hero-photo" role="img" aria-label="Photograph of a flexed muscular arm against a dark background"></div>
    <div class="title-the">The</div>
    <div class="title-name">Holl</div>
    <section class="band">
    </section>
    <div class="brand-name">KOR</div>
    <p class="tagline">Building <span class="tagline-strong">HOLLEN</span> muscles</p>
  </main>
</body>
</html>
```